Rig up a website for a Rigging Company

We already have a logo. Looking for a website design that works on pavlune.com.
Our rigging company uses semi trucks, forklifts, and similar equipment to move large machines.
Our logo is white, black and red.

Target Market(s)

Medical Industry (moving medical equipment), Utility Industry (power equipment), Food Industry (moving bottling/packing equipment), US Government (large equipment)

Industry/Entity Type

It Company

Coding

Coded - Design and coding required

Number of Pages Required

5+ page

Font styles to use
Sans Serif

Colors
ec1f27
ffffff
0355a3

Requirements
Must have
• Home page, About page, Services Page, and Contact Information page
Nice to have
• Pictures of semi and forklifts and ability to insert our own pictures of our equipment

```html
<!DOCTYPE html>
<html lang="en">
<head>
<meta charset="utf-8">
<title>Harlow Rigging</title>
<link href="https://fonts.googleapis.com/css2?family=Nunito+Sans:wght@700;800;900&family=Open+Sans:ital,wght@0,400;0,600;0,700;1,400&display=swap" rel="stylesheet">
<style>
:root{
  --red:#ec1f27;
  --blue:#0355a3;
  --ink:#1d1d1d;
  --text:#555;
  --muted:#8a8a8a;
  --line:#e3e3e3;
  --white:#fff;
  --pale:#eef0f4;
  --dark:#232323;
}
*{margin:0;padding:0;box-sizing:border-box}
html,body{width:1200px;height:2436px;overflow:hidden}
body{position:relative;background:var(--white);font-family:"Open Sans",Arial,sans-serif;color:var(--text)}
.abs{position:absolute}
.heading{font-family:"Nunito Sans",Arial,sans-serif;font-weight:800;color:var(--ink);letter-spacing:.3px}
.btn{position:absolute;display:flex;align-items:center;justify-content:center;border:2px solid #cfcfcf;border-radius:20px;color:var(--red);font-size:13px;font-weight:700;background:var(--white)}
/* header */
.brand{position:absolute;display:flex;align-items:center;gap:10px;font-family:"Nunito Sans",Arial,sans-serif;font-weight:900;font-size:34px;color:var(--ink)}
.brand .mark{width:26px;height:26px;background:var(--red)}
.contact-top{position:absolute;top:16px;display:flex;align-items:center;gap:10px;font-size:17px;color:var(--ink)}
.nav{position:absolute;top:62px;right:98px;display:flex;gap:34px;font-size:15px;font-weight:600;color:var(--ink)}
.nav .active{color:var(--red)}
/* hero */
.hero{position:absolute;left:0;top:92px;width:1200px;height:457px;background:linear-gradient(180deg,#2e5d9a 0%,#6f95c4 55%,#b7c7d6 100%)}
.hero-title{position:absolute;top:200px;width:100%;text-align:center;font-family:"Nunito Sans",Arial,sans-serif;font-weight:800;font-size:66px;color:var(--white)}
.hero-sub{position:absolute;top:290px;width:100%;text-align:center;font-size:20px;line-height:34px;color:var(--white)}
.hero-btn{position:absolute;left:512px;top:382px;width:177px;height:38px;border-radius:20px;background:var(--red);color:var(--white);font-weight:700;font-size:15px;display:flex;align-items:center;justify-content:center}
.dots{position:absolute;top:493px;left:561px;display:flex;gap:8px}
.dots span{width:14px;height:14px;border-radius:50%;border:2px solid var(--white)}
.dots span.on{background:var(--white)}
/* welcome */
.body-copy{font-size:13px;line-height:25px;color:var(--text)}
.video{position:absolute;left:638px;top:609px;width:463px;height:284px;border:4px solid #f3f3f3;box-shadow:0 0 0 1px #ddd;background:linear-gradient(180deg,#6b9bd8 0%,#98b9df 50%,#8c7a62 80%,#6e6253 100%)}
.play{position:absolute;left:207px;top:113px;width:56px;height:56px;border-radius:50%;background:rgba(0,0,0,.75)}
/* services */
.services{position:absolute;top:950px;left:0;width:1200px;height:440px;background:linear-gradient(90deg,#f1e6e6 0%,#eef0f4 40%,#eef0f4 70%,#e3e6ec 100%)}
.svc{position:absolute;top:100px;width:320px;text-align:center}
.svc h3{margin-top:22px;font-family:"Nunito Sans",Arial,sans-serif;font-weight:800;font-size:19px;color:var(--ink)}
.svc p{margin-top:6px;font-size:12.5px;line-height:23px;color:var(--text)}
/* why/blog */
.ticks{position:absolute;left:100px;top:1578px;list-style:none}
.ticks li{display:flex;align-items:center;gap:14px;height:36.5px;font-size:12.5px;color:var(--text)}
.tick{width:15px;height:15px;border-radius:50%;background:var(--red);flex:none}
.post{position:absolute;left:588px;width:514px}
.thumb{position:absolute;left:0;top:0;width:150px;height:114px;border:3px solid #f3f3f3;box-shadow:0 0 0 1px #ddd}
.post h4{position:absolute;left:174px;top:0;font-family:"Nunito Sans",Arial,sans-serif;font-weight:700;font-size:20px;color:var(--ink);white-space:nowrap}
.meta{position:absolute;left:174px;top:38px;display:flex;gap:16px;font-size:12px;font-style:italic;color:var(--muted)}
.meta b{display:inline-block;width:9px;height:9px;background:var(--red);margin-right:6px}
.post p{position:absolute;left:174px;top:62px;width:340px;font-size:12.5px;line-height:23px;color:var(--text)}
/* testimonial */
.testimonial{position:absolute;left:0;top:1920px;width:1200px;height:164px;background:linear-gradient(90deg,#8d8d8d 0%,#6e6e6e 40%,#555 70%,#3f3f3f 100%)}
.quote{position:absolute;left:313px;top:36px;width:690px;font-size:13px;line-height:24px;font-style:italic;color:var(--white)}
.author{position:absolute;left:313px;top:104px;font-size:14px;font-weight:700;color:var(--white)}
/* footer */
.foot-h{position:absolute;top:2147px;font-family:"Nunito Sans",Arial,sans-serif;font-weight:800;font-size:15px;color:var(--ink);letter-spacing:.4px}
.foot-links{position:absolute;left:409px;top:2187px;list-style:none;font-size:12.5px;line-height:24px;color:var(--text)}
.foot-row{position:absolute;left:914px;display:flex;gap:20px;font-size:12.5px;line-height:19px;color:var(--text)}
.foot-row i{width:10px;height:12px;background:var(--red);flex:none;margin-top:3px}
.bottom{position:absolute;left:0;top:2371px;width:1200px;height:65px;background:var(--dark)}
.bottom .red{position:absolute;left:0;top:0;height:65px;width:660px;background:var(--red);clip-path:polygon(0 0,620px 0,660px 65px,0 65px)}
.social{position:absolute;left:974px;top:20px;display:flex;gap:8px}
.social span{width:25px;height:25px;border-radius:50%;border:1.5px solid var(--white)}
</style>
</head>
<body>

<header>
  <div class="brand" style="left:100px;top:22px"><span class="mark"></span>Harlow Rigging</div>
  <div class="contact-top" style="left:704px">
    <svg width="22" height="22" viewBox="0 0 24 24"><path fill="#ec1f27" d="M6.6 10.8a15.1 15.1 0 006.6 6.6l2.2-2.2a1 1 0 011-.25 11.4 11.4 0 003.6.57 1 1 0 011 1V20a1 1 0 01-1 1A17 17 0 013 4a1 1 0 011-1h3.5a1 1 0 011 1 11.4 11.4 0 00.57 3.6 1 1 0 01-.25 1z"/></svg>
    <span>1 800 555 0142</span>
  </div>
  <div class="contact-top" style="left:894px">
    <svg width="22" height="16" viewBox="0 0 22 16"><rect width="22" height="16" rx="2" fill="#ec1f27"/><path d="M1 1l10 8 10-8" stroke="#fff" stroke-width="1.6" fill="none"/></svg>
    <span>info@pavlune.com</span>
  </div>
  <nav class="nav">
    <span class="active">HOME</span><span>ABOUT US</span><span>SERVICES</span><span>EQUIPMENT</span><span>BLOG</span><span>CONTACT US</span>
    <svg width="14" height="14" viewBox="0 0 14 14"><circle cx="6" cy="6" r="4.5" stroke="#1d1d1d" stroke-width="2" fill="none"/><path d="M9.5 9.5L13 13" stroke="#1d1d1d" stroke-width="2"/></svg>
  </nav>
</header>

<section class="hero" role="img" aria-label="Photo of a yellow crane lifting a large machine crate against a blue sky">
  <h1 class="hero-title">HARLOW RIGGING</h1>
  <p class="hero-sub">We are a rigging company. Our rigging company uses semi trucks, forklifts,<br>and similar equipment to move large machines.</p>
  <div class="hero-btn">GET A QUOTE</div>
  <div class="dots"><span class="on"></span><span></span><span></span><span></span></div>
</section>

<section>
  <h2 class="heading abs" style="left:97px;top:604px;font-size:26px">WELCOME TO HARLOW RIGGING</h2>
  <p class="body-copy abs" style="left:97px;top:656px;width:492px">At vero eos et accusamus et iusto odio dignissimos ducimus qui blanditiis prasentium voluptatum deleniti atque corrupti quos.</p>
  <p class="body-copy abs" style="left:97px;top:731px;width:492px">Dolores et quas molestias excepturi sint occaecati cupiditate non provi similiquei sunt in culpa qui officia deserunt mollitia animi, id est laborum et dolorum fugha rum quidem rerum facilis est et expedita distinctio um soluta nobis est eligendop tio cumque nihil impedit quo minus id quod quib.</p>
  <div class="btn" style="left:97px;top:855px;width:130px;height:35px">READ MORE &gt;&gt;</div>
  <div class="video" role="img" aria-label="Video still of a reach stacker forklift lifting a tank container onto a trailer">
    <div class="play"><svg width="56" height="56" viewBox="0 0 56 56"><path d="M22 17l18 11-18 11z" fill="#fff"/></svg></div>
  </div>
</section>

<section class="services" role="img" aria-label="Faded background photo of a red crane lattice">
  <h2 class="heading abs" style="left:0;width:1200px;text-align:center;top:52px;font-size:26px">OUR SERVICES</h2>

  <div class="svc" style="left:80px">
    <svg width="90" height="92" viewBox="0 0 90 92"><rect x="40" y="0" width="10" height="10" fill="#ec1f27"/><path d="M45 10v10M30 38l15-16 15 16" stroke="#ec1f27" stroke-width="3" fill="none"/><rect x="4" y="40" width="82" height="50" fill="#ec1f27"/><path d="M16 46v38M28 46v38M40 46v38M52 46v38M64 46v38M76 46v38" stroke="#fff" stroke-width="2"/></svg>
    <h3>RIGGING</h3>
    <p>At vero eos et accusamus et iusto odio digniss<br>imos ducimus qui blanditiis praesentium voluptatu<br>deleniti atque corrupti quos dolorero</p>
  </div>
  <div class="svc" style="left:441px">
    <svg width="136" height="92" viewBox="0 0 136 92"><rect x="46" y="18" width="88" height="52" fill="#ec1f27"/><path d="M68 18v52M90 18v52M112 18v52M46 44h88" stroke="#fff" stroke-width="2"/><path d="M4 70V42l12-18h26v46z" fill="#ec1f27"/><path d="M12 42l8-12h14v12z" fill="#fff"/><rect x="2" y="70" width="134" height="6" fill="#ec1f27"/><circle cx="24" cy="80" r="11" fill="#fff" stroke="#ec1f27" stroke-width="6"/><circle cx="112" cy="80" r="11" fill="#fff" stroke="#ec1f27" stroke-width="6"/></svg>
    <h3>TRUCKING</h3>
    <p>At vero eos et accusamus et iusto odio digniss<br>imos ducimus qui blanditiis praesentium voluptatu<br>deleniti atque corrupti quos dolorero</p>
  </div>
  <div class="svc" style="left:798px">
    <svg width="100" height="92" viewBox="0 0 100 92"><path d="M6 4v70h22" stroke="#ec1f27" stroke-width="7" fill="none"/><rect x="10" y="24" width="22" height="22" fill="#ec1f27"/><path d="M40 74V40h24l14 18h18v16z" fill="#ec1f27"/><rect x="46" y="44" width="14" height="14" fill="#fff"/><circle cx="52" cy="78" r="10" fill="#fff" stroke="#ec1f27" stroke-width="6"/><circle cx="86" cy="78" r="10" fill="#fff" stroke="#ec1f27" stroke-width="6"/></svg>
    <h3>MACHINERY MOVING</h3>
    <p>At vero eos et accusamus et iusto odio digniss<br>imos ducimus qui blanditiis praesentium voluptatu<br>deleniti atque corrupti quos dolorero</p>
  </div>

  <div class="btn" style="left:172px;top:354px;width:138px;height:33px">READ MORE &gt;&gt;</div>
  <div class="btn" style="left:532px;top:354px;width:138px;height:33px">READ MORE &gt;&gt;</div>
  <div class="btn" style="left:890px;top:354px;width:138px;height:33px">READ MORE &gt;&gt;</div>
</section>

<section>
  <h2 class="heading abs" style="left:100px;top:1449px;font-size:26px">WHY CHOOSE HARLOW RIGGING</h2>
  <p class="body-copy abs" style="left:100px;top:1510px;width:450px;font-size:12.5px;line-height:24px">Temporibus autem quibusdam et aut officiis debitis aut rerum necessitatibus saepe eveniet ut et voluptates repudiandae sint .</p>
  <ul class="ticks">
    <li><span class="tick"></span>Blanditiis praesentium voluptatum deleniti atque corrupti quos</li>
    <li><span class="tick"></span>Sed ut perspiciatis unde omnis iste natus error sit voluptatem accus</li>
    <li><span class="tick"></span>But I must explain to you how all this mistaken idea of denouncing</li>
    <li><span class="tick"></span>Nemo enim ipsam voluptatem quia voluptas sit aspernatur</li>
    <li><span class="tick"></span>At vero eos et accusamus et iusto odio dignissimos ducimus qui</li>
    <li><span class="tick"></span>Nam libero tempore, cum soluta nobis est eligendi optio cumque nihil</li>
  </ul>
  <div class="btn" style="left:100px;top:1817px;width:137px;height:33px">READ MORE &gt;&gt;</div>

  <h2 class="heading abs" style="left:588px;top:1449px;font-size:26px">OUR BLOG</h2>
  <article class="post" style="top:1518px">
    <div class="thumb" role="img" aria-label="Photo of a flatbed truck hauling heavy machinery on a road" style="background:linear-gradient(180deg,#7fa6d6 0%,#a9a38a 55%,#6d6a66 100%)"></div>
    <h4>At vero eos et accusamus et iustoserti</h4>
    <div class="meta"><span><b></b>15/10/2015</span><span><b></b>John Doe</span><span><b></b>4 Comments</span></div>
    <p>Duis aute irure dolor in reprehenderit in voluptate velit esse cillum dolore eu fugiat nulla pariatur.</p>
  </article>
  <div class="abs" style="left:588px;top:1653px;width:514px;height:1px;background:var(--line)"></div>
  <article class="post" style="top:1673px">
    <div class="thumb" role="img" aria-label="Photo of a reach stacker loading a container onto a truck" style="background:linear-gradient(180deg,#6f9bd3 0%,#9ab4d2 55%,#7a6d5c 100%)"></div>
    <h4>At vero eos et accusamus et iustoserti</h4>
    <div class="meta"><span><b></b>15/10/2015</span><span><b></b>John Doe</span><span><b></b>4 Comments</span></div>
    <p>Duis aute irure dolor in reprehenderit in voluptate velit esse cillum dolore eu fugiat nulla pariatur.</p>
  </article>
  <div class="abs" style="left:588px;top:1807px;width:514px;height:1px;background:var(--line)"></div>
  <div class="btn" style="left:588px;top:1825px;width:138px;height:33px">VIEW MORE &gt;&gt;</div>
</section>

<section class="testimonial" role="img" aria-label="Dark background photo of a crane boom and lifting hook">
  <svg class="abs" style="left:38px;top:62px" width="24" height="40" viewBox="0 0 24 40"><path d="M20 2L4 20l16 18" stroke="#fff" stroke-width="4" fill="none"/></svg>
  <svg class="abs" style="left:1138px;top:62px" width="24" height="40" viewBox="0 0 24 40"><path d="M4 2l16 18L4 38" stroke="#fff" stroke-width="4" fill="none"/></svg>
  <div class="abs" style="left:138px;top:40px;width:80px;height:80px;border-radius:50%;background:#c9c9c9"></div>
  <svg class="abs" style="left:160px;top:66px" width="36" height="28" viewBox="0 0 36 28"><path d="M2 28V14C2 6 7 2 14 1v5c-4 1-6 4-6 8h6v14zM22 28V14c0-8 5-12 12-13v5c-4 1-6 4-6 8h6v14z" fill="#eee"/></svg>
  <div class="abs" role="img" aria-label="Portrait of the reviewer" style="left:196px;top:40px;width:80px;height:80px;border-radius:50%;border:3px solid #fff;background:linear-gradient(180deg,#d9d9d9,#9a9a9a)"></div>
  <p class="quote">At vero eos et accusamus et iusto odio dignissimos ducimus qui blanditiis praesentium voluptatum deleniti atque corrupti quos dolores et quas molestias excepturi sint occaecati cupiditate non provident, similique sun</p>
  <p class="author">- Delorme, English Instructor</p>
</section>

<footer>
  <div class="brand" style="left:100px;top:2222px;font-size:36px"><span class="mark"></span>Harlow Rigging</div>

  <h3 class="foot-h" style="left:409px">INFORMATION</h3>
  <ul class="foot-links"><li>Home</li><li>About Us</li><li>Services</li><li>Equipment</li><li>Blog</li><li>Contact Us</li></ul>

  <h3 class="foot-h" style="left:580px">NEWSLETTER SUBSCRIPTION</h3>
  <p class="abs" style="left:580px;top:2187px;width:270px;font-size:12.5px;line-height:22px">Register your Email Address to get Information about us</p>
  <p class="abs" style="left:594px;top:2245px;font-size:12px;color:var(--muted)">Email Address</p>
  <div class="abs" style="left:580px;top:2270px;width:255px;height:1px;background:#cfcfcf"></div>
  <div class="btn" style="left:580px;top:2292px;width:119px;height:31px;color:var(--ink)">SUBSCRIBE</div>

  <h3 class="foot-h" style="left:914px">GET IN TOUCH</h3>
  <div class="foot-row" style="top:2188px"><i></i><span>12 Harbour View Road<br>Northport, NL A1B 2C3</span></div>
  <div class="foot-row" style="top:2243px"><i></i><span>1-888-888-8888</span></div>
  <div class="foot-row" style="top:2279px"><i></i><span>1-222-222-2222</span></div>
  <div class="foot-row" style="top:2315px"><i></i><span>info@pavlune.com</span></div>

  <div class="bottom">
    <div class="red"></div>
    <p class="abs" style="left:100px;top:25px;font-size:12px;color:var(--white)">Copyrights © 2017, Harlow Rigging. All rights reserved.</p>
    <div class="social"><span></span><span></span><span></span><span></span></div>
  </div>
</footer>

</body>
</html>
```